Create a Poster Campaign for a Zurich-based Crowdfinancing Startup

Company: Brightmoor Kapital GmbH (bmk-lend.ch)
Campaign: First major marketing push
Scope: Billboard posters

Company description:
Brightmoor Kapital GmbH is a crowdfinancing platform, where people and businesses needing money can raise funds in three different ways: 1. Crowdlending (borrowing and paying interest), 2. Crowdfactoring for businesses (pre-financing an open invoice), 3. Crowdfunding (rewards-based funding). What Brightmoor Kapital from the competitors differentiates is that borrowers can borrow at their own conditions (amount, duration up to 5 years, and interest rate).
MORE INFO: www.bmk-lend.ch

We are also changing website colours to blue away from brown.

Need:
We need to attract more users to the platform and because we only operate in Switzerland, a poster campaign is meant to create awareness of our brand and services.

We need 2 posters designs in F 200 and F 24 Large Format (Here is a tool to see poster sizes (https://booking.velorapost.ch/en/poster-design-tips-and-checklist)

Notes:
We would like to use bmk-lend.ch as the name and address of the platform. We do not want plant motifs (growth of a plant from dirt, or money growing).

Slogan Ideas:
Too much money? Not enough money? Come to BMK.

We’ve got your next loan.

Balanced for borrowers and lenders. <— potentially a secondary text block

Target Market(s)

People who need money (businesses and private people) as well as people and businesses looking to invest money. It needs to speak to both.

Industry/Entity Type

Financial

Font styles to use
Serif
Sans Serif

Colors
0355a3
3276b5
85acd3
cedeed

Requirements
Must have
• Message and headline: must get across in 1–2 seconds, be catchy and easy to grasp
• Few words: maximum of ten
• Font size should make text readable up to ten metres
• High contrast dark on light and complementary colours are easiest to take in
• Logo must be clearly recognizable.
• Elements essential to the image, such as texts, should be placed at least 6 cm – in the case of F12 and F24 – and 4 cm – in the case of F4 and F200 formats – from the edge at the top, bottom and sides (this is mandatory in the case of posters placed in light boxes).
Nice to have
• Kelvo and Lendra Square have done some creative posters.
Should not have
• No plant images

```html
<!DOCTYPE html>
<html lang="de">
<head>
<meta charset="utf-8">
<title>Brightmoor Kapital – Plakat</title>
<link rel="stylesheet" href="https://fonts.googleapis.com/css2?family=Oswald:wght@600;700&family=Montserrat:wght@600&display=swap">
<style>
  :root {
    --navy: #0f4c8f;
    --cyan: #1cc6f0;
    --white: #ffffff;
    --photo-light: #e9ebee;
    --photo-mid: #c9ccd1;
  }
  html, body {
    margin: 0;
    padding: 0;
    width: 869px;
    height: 1200px;
    overflow: hidden;
    background: var(--white);
  }
  .poster {
    position: relative;
    width: 869px;
    height: 1200px;
    background: var(--white);
    overflow: hidden;
    font-family: "Oswald", "Arial Narrow", sans-serif;
  }
  .photo {
    position: absolute;
  }
  .photo--lender {
    left: 54px;
    top: 29px;
    width: 370px;
    height: 530px;
    background: radial-gradient(ellipse at 45% 45%, var(--photo-mid) 0%, var(--photo-light) 55%, var(--white) 100%);
  }
  .photo--borrower {
    left: 395px;
    top: 466px;
    width: 474px;
    height: 520px;
    background: radial-gradient(ellipse at 60% 55%, var(--photo-mid) 0%, var(--photo-light) 55%, var(--white) 100%);
  }
  .headline {
    position: absolute;
    margin: 0;
    font-weight: 700;
    font-size: 128px;
    line-height: 113px;
    letter-spacing: -1px;
    text-transform: uppercase;
  }
  .headline span { display: block; }
  .headline .dark { color: var(--navy); }
  .headline .light { color: var(--cyan); }
  .headline--lender {
    right: 29px;
    top: 102px;
    text-align: right;
  }
  .headline--borrower {
    left: 50px;
    top: 555px;
    text-align: left;
  }
  .footer-band {
    position: absolute;
    left: 0;
    bottom: 0;
    width: 869px;
    height: 214px;
    background: var(--navy);
  }
  .tagline {
    position: absolute;
    left: 45px;
    top: 32px;
    margin: 0;
    font-family: "Montserrat", Arial, sans-serif;
    font-weight: 600;
    font-size: 21px;
    line-height: 31px;
    color: var(--white);
  }
  .cta {
    position: absolute;
    left: 45px;
    top: 90px;
    margin: 0;
    color: var(--cyan);
    font-weight: 600;
    white-space: nowrap;
  }
  .cta-lead { font-size: 34px; }
  .cta-url { font-size: 54px; margin-left: 8px; }
  .brand {
    position: absolute;
    left: 560px;
    top: 46px;
    display: flex;
    align-items: center;
    gap: 18px;
  }
  .brand-dot {
    width: 86px;
    height: 86px;
    border-radius: 50%;
    background: var(--white);
    flex: none;
  }
  .brand-name {
    font-weight: 600;
    font-size: 40px;
    line-height: 42px;
    color: var(--white);
  }
</style>
</head>
<body>
  <main class="poster">
    <div class="photo photo--lender" role="img" aria-label="Lächelnder Mann im hellen Anzug, der Geldscheine hinhält"></div>
    <div class="photo photo--borrower" role="img" aria-label="Junge Frau, die besorgt in ihr leeres Portemonnaie schaut"></div>

    <h1 class="headline headline--lender">
      <span class="dark">Zu viel</span>
      <span class="light">Geld?</span>
    </h1>

    <h2 class="headline headline--borrower">
      <span class="dark">Nicht</span>
      <span class="dark">genug</span>
      <span class="light">Geld?</span>
    </h2>

    <footer class="footer-band">
      <p class="tagline">Der perfekte Ausgleich für<br>Kreditnehmer und Kreditgeber</p>
      <p class="cta"><span class="cta-lead">Besuchen Sie</span><span class="cta-url">bmk-lend.ch</span></p>
      <div class="brand">
        <span class="brand-dot"></span>
        <span class="brand-name">Brightmoor<br>Kapital</span>
      </div>
    </footer>
  </main>
</body>
</html>
```